High Tech Real Estate Startup needs a business card

We are developing an innovative real estate marketing product based around advanced search and virtual reality.

We talk to people, we need business cards.

Target Market(s)

The target market is technology professionals and realtors.

Contact Information for Business Card

The information to be included will include

Name
Title
Phone Number
E-mail Address
www.zelquin.com

It should use simple iconography for each one of those fields.

Font styles to use
Other font styles liked:
• Co, Jubilat, Avenir

Colors

Designer to choose colors to be used in the design.

Requirements
Must have
• Clean aesthetic,
• Good use of negative space.
• It should use our company logo, shown in the attached file. It is able to use the negative of that logo (coloured font and white background) and I have attached other acceptable accent colours in a swatch file.
Should not have
• Should not be too busy
• No extraneous text (slogans, tag lines etc)

```html
<!DOCTYPE html>
<html lang="en">
<head>
<meta charset="UTF-8">
<title>Zelquin Business Card</title>
<link rel="stylesheet" href="https://fonts.googleapis.com/css2?family=Work+Sans:wght@400;500;600&display=swap">
<style>
  :root {
    --backdrop: #1b1b1c;
    --card: #202021;
    --card-edge: #262627;
    --teal: #14bcc1;
    --ink: #f2f2f2;
  }
  * { margin: 0; padding: 0; box-sizing: border-box; }
  html, body { width: 1200px; height: 900px; overflow: hidden; }
  body {
    background: var(--backdrop);
    font-family: "Work Sans", sans-serif;
    color: var(--ink);
    position: relative;
  }
  .card {
    position: absolute;
    left: 250px;
    width: 700px;
    height: 400px;
    background: linear-gradient(135deg, var(--card) 0%, var(--card-edge) 100%);
    border-bottom: 7px solid var(--teal);
  }
  .card--back { top: 35px; }
  .card--front { top: 465px; }

  .brand {
    display: flex;
    align-items: center;
    gap: 14px;
  }
  .brand__mark { background: var(--teal); flex: none; }
  .brand__name {
    color: var(--ink);
    font-weight: 500;
    letter-spacing: 0.06em;
  }
  .card--back .brand {
    position: absolute;
    left: 50%;
    top: 50%;
    transform: translate(-50%, -50%);
  }
  .card--back .brand__mark { width: 44px; height: 44px; }
  .card--back .brand__name { font-size: 28px; }

  .card--front .brand {
    position: absolute;
    left: 50px;
    top: 176px;
  }
  .card--front .brand__mark { width: 40px; height: 40px; }
  .card--front .brand__name { font-size: 30px; }

  .divider {
    position: absolute;
    left: 318px;
    top: 80px;
    width: 3px;
    height: 230px;
    background: var(--teal);
  }
  .details {
    position: absolute;
    left: 362px;
    top: 86px;
  }
  .details__name {
    color: var(--teal);
    font-size: 28px;
    font-weight: 500;
    letter-spacing: 0.02em;
    line-height: 1;
  }
  .details__title { font-size: 19px; margin-top: 6px; letter-spacing: 0.04em; }
  .details__address {
    font-style: normal;
    font-size: 19px;
    line-height: 1.3;
    margin-top: 18px;
    letter-spacing: 0.04em;
  }
  .contact { list-style: none; margin-top: 8px; }
  .contact__item {
    display: flex;
    align-items: center;
    gap: 12px;
    font-size: 19px;
    line-height: 1.4;
    letter-spacing: 0.04em;
  }
  .contact__icon { width: 14px; height: 14px; flex: none; }
</style>
</head>
<body>
  <section class="card card--back" aria-label="Card back">
    <div class="brand">
      <span class="brand__mark"></span>
      <span class="brand__name">ZELQUIN</span>
    </div>
  </section>

  <section class="card card--front" aria-label="Card front">
    <div class="brand">
      <span class="brand__mark"></span>
      <span class="brand__name">ZELQUIN</span>
    </div>
    <div class="divider"></div>
    <div class="details">
      <h1 class="details__name">DORIAN KESSEL</h1>
      <p class="details__title">Director</p>
      <address class="details__address">742 Alder Ridge Ln.<br>Franklin, TN 37064</address>
      <ul class="contact">
        <li class="contact__item">
          <svg class="contact__icon" viewBox="0 0 16 16" fill="none" stroke="#14bcc1" stroke-width="1.6" aria-hidden="true">
            <path d="M4 1.5l2.5 3-1.5 1.5c.8 2 2.5 3.7 4.5 4.5l1.5-1.5 3 2.5-1.5 2.5C7 14 2 9 1.5 3z"/>
          </svg>
          <span>+1-555-204-7781</span>
        </li>
        <li class="contact__item">
          <svg class="contact__icon" viewBox="0 0 16 16" fill="none" stroke="#14bcc1" stroke-width="1.5" aria-hidden="true">
            <rect x="1" y="3" width="14" height="10"/>
            <path d="M1 3l7 6 7-6"/>
          </svg>
          <span>info@zelquin.com</span>
        </li>
        <li class="contact__item">
          <svg class="contact__icon" viewBox="0 0 16 16" fill="none" stroke="#14bcc1" stroke-width="1.3" aria-hidden="true">
            <circle cx="8" cy="8" r="6.5"/>
            <ellipse cx="8" cy="8" rx="3" ry="6.5"/>
            <path d="M1.5 8h13M2.5 4.5h11M2.5 11.5h11"/>
          </svg>
          <span>www.zelquin.com</span>
        </li>
      </ul>
    </div>
  </section>
</body>
</html>
```